Wandering Rooms Stationary Set

Wandering Rooms is a bespoke interior design firm set to provide services to VIP clients with elegance and minimalism is the main theme for our stationary set. We require a full stationary set covering A4 letterhead, A4 & A3 envelopes, business cards, USB's, CDs, email signature and any other item the designer sees fit. logo is already designed and finalized, and we require the designer to use it as is without modifying the logo.

Address to be used on letterhead / business cards ...etc shall be as follows:

Phone : +971 2 518 2047
P.O. Box : 309186
Address: Block C&D, Bldg. 47, Court 12, Abu Dhabi, United Arab Emirates
Website: www.wanderingrooms-example.com

Target Market(s)

VIP Clients

Industry/Entity Type

Interior Design

Font styles to use
Other font styles liked:
• something to be unique

Colors

Designer to choose colors to be used in the design.

Requirements
Must have
• Elegant, minimalistic
Nice to have
• Simple yet elegant design having a sharp yet clean cut format
Should not have
• No additional colours, just colours that are used in the logo (silver, black or gold)

```html
<!DOCTYPE html>
<html lang="en">
<head>
<meta charset="utf-8">
<title>Wandering Rooms – Envelope</title>
<link rel="stylesheet" href="https://fonts.googleapis.com/css2?family=Cormorant+Garamond:wght@500&family=Montserrat:wght@400&display=swap">
<style>
  :root {
    --backdrop: #6e6e6e;
    --paper: #464646;
    --paper-edge: #3d3d3d;
    --paper-inside: #3a3a3a;
    --gold: #b9a56d;
    --gold-light: #cbb985;
    --gold-deep: #9c8a55;
    --tone-on-tone: #4d4d4d;
  }
  * { margin: 0; padding: 0; box-sizing: border-box; }
  html, body {
    width: 1200px;
    height: 1048px;
    overflow: hidden;
    background: var(--backdrop);
  }
  .canvas {
    position: relative;
    width: 1200px;
    height: 1048px;
  }

  /* Envelope back with open gold-lined flap */
  .envelope-back {
    position: absolute;
    left: 130px;
    top: 300px;
    width: 440px;
    height: 622px;
    background: var(--paper);
    border: 1px solid var(--paper-edge);
  }
  .envelope-back__flap {
    position: absolute;
    left: 130px;
    top: 196px;
    width: 440px;
    height: 104px;
    background: linear-gradient(180deg, var(--gold-light), var(--gold));
    border-radius: 10px 10px 0 0;
  }
  .envelope-back__mouth {
    position: absolute;
    left: 130px;
    top: 300px;
    width: 440px;
    height: 26px;
    background: linear-gradient(180deg, var(--gold-deep), var(--paper-inside));
  }
  .envelope-back__seam {
    position: absolute;
    left: 130px;
    top: 326px;
    width: 440px;
    height: 1px;
    background: var(--paper-edge);
  }

  /* Envelope front */
  .envelope-front {
    position: absolute;
    left: 630px;
    top: 270px;
    width: 440px;
    height: 622px;
    background: var(--paper);
    border: 1px solid var(--paper-edge);
    overflow: hidden;
  }
  .envelope-front__accent {
    position: absolute;
    right: -150px;
    top: 140px;
    width: 420px;
    height: 420px;
    border-radius: 50%;
    border: 3px solid var(--tone-on-tone);
  }
  .brand {
    position: absolute;
    left: 34px;
    top: 36px;
    font-family: "Cormorant Garamond", Georgia, serif;
    font-weight: 500;
    font-size: 15px;
    letter-spacing: 0.22em;
    text-transform: uppercase;
    color: var(--gold);
  }
  .address {
    position: absolute;
    left: 34px;
    bottom: 30px;
    padding-left: 9px;
    border-left: 2px solid var(--gold);
    font-family: "Montserrat", Arial, sans-serif;
    font-weight: 400;
    font-size: 8px;
    line-height: 1.35;
    color: var(--gold);
    font-style: normal;
  }
</style>
</head>
<body>
  <main class="canvas">
    <div class="envelope-back__flap"></div>
    <div class="envelope-back"></div>
    <div class="envelope-back__mouth"></div>
    <div class="envelope-back__seam"></div>

    <section class="envelope-front">
      <div class="envelope-front__accent"></div>
      <p class="brand">Wandering Rooms</p>
      <address class="address">
        Block C&amp;D, Bldg. 47, Court 12<br>
        Abu Dhabi, United Arab Emirates<br>
        P.O. Box: 309186
      </address>
    </section>
  </main>
</body>
</html>
```